Cafe Business needs a business card design

I already have an ai logo I would like to use and color. I need someone to make a business card for me on adobe illustrator with it. Its for a cafe restaurant opening in Japan I would like to be able to change out the names, contact info, ect on my own from adobe illustrator.

Industry/Entity Type

Business

Contact Information for Business Card

Double sided with logo on one side and info on the other. Name, Tel, fax, email and west

```html
<!DOCTYPE html>
<html lang="en">
<head>
<meta charset="utf-8">
<title>Sora Bean Cafe – Business Card</title>
<link rel="stylesheet" href="https://fonts.googleapis.com/css2?family=Open+Sans:wght@400;600;700&display=swap">
<style>
  :root {
    --espresso: #3b2518;
    --espresso-deep: #2a170e;
    --cream: #f1e3cf;
    --cream-light: #faf3e8;
    --paper: #ffffff;
    --ink: #4a3325;
    --backdrop: #e9e4de;
  }
  * { margin: 0; padding: 0; box-sizing: border-box; }
  html, body {
    width: 1200px;
    height: 913px;
    overflow: hidden;
    background: var(--backdrop);
    font-family: "Open Sans", sans-serif;
  }
  .canvas {
    position: relative;
    width: 1200px;
    height: 913px;
  }
  .card {
    position: absolute;
    top: 302px;
    width: 540px;
    height: 309px;
    border-radius: 18px;
    overflow: hidden;
    box-shadow: 0 6px 22px rgba(40, 25, 15, 0.22);
  }
  .card--info { left: 40px; }
  .card--logo { left: 620px; background: var(--paper); }
  .card__art {
    position: absolute;
    inset: 0;
    width: 100%;
    height: 100%;
  }

  .brand {
    position: absolute;
    display: flex;
    flex-direction: column;
    align-items: center;
    gap: 10px;
  }
  .brand__square {
    width: 96px;
    height: 96px;
  }
  .brand__name {
    font-weight: 700;
    font-size: 22px;
    letter-spacing: 1.5px;
    line-height: 1;
    white-space: nowrap;
  }
  .card--info .brand { left: 34px; top: 74px; }
  .card--info .brand__square { background: var(--paper); }
  .card--info .brand__name { color: var(--paper); }
  .card--logo .brand { right: 48px; top: 30px; }
  .card--logo .brand__square { background: var(--espresso); }
  .card--logo .brand__name { color: var(--espresso); }

  .contact {
    position: absolute;
    right: 24px;
    top: 92px;
    text-align: right;
    color: var(--ink);
  }
  .contact__name {
    font-size: 18px;
    font-weight: 600;
    letter-spacing: 0.5px;
  }
  .contact__role {
    font-size: 11px;
    letter-spacing: 1px;
    margin-bottom: 8px;
    margin-right: 19px;
  }
  .contact__list { list-style: none; }
  .contact__item {
    display: flex;
    justify-content: flex-end;
    align-items: center;
    gap: 7px;
    font-size: 11.5px;
    line-height: 20px;
    white-space: nowrap;
  }
  .contact__icon {
    width: 12px;
    height: 12px;
    fill: none;
    stroke: var(--ink);
    stroke-width: 1.4;
    stroke-linecap: round;
    stroke-linejoin: round;
  }
</style>
</head>
<body>
<main class="canvas">

  <section class="card card--info">
    <svg class="card__art" viewBox="0 0 540 309" preserveAspectRatio="none" aria-hidden="true">
      <defs>
        <linearGradient id="cream-fade" x1="0" y1="0" x2="1" y2="1">
          <stop offset="0" stop-color="#faf3e8"/>
          <stop offset="1" stop-color="#ead8bf"/>
        </linearGradient>
        <linearGradient id="espresso-fade" x1="0" y1="0" x2="1" y2="1">
          <stop offset="0" stop-color="#2a170e"/>
          <stop offset="1" stop-color="#4a2e1d"/>
        </linearGradient>
      </defs>
      <rect width="540" height="309" fill="url(#cream-fade)"/>
      <path d="M0 0 H262 C356 70 364 230 282 309 H0 Z" fill="url(#espresso-fade)"/>
      <path d="M270 0 C364 72 372 232 290 309" fill="none" stroke="#ffffff" stroke-width="5"/>
    </svg>

    <div class="brand">
      <span class="brand__square"></span>
      <span class="brand__name">SORA BEAN CAFE</span>
    </div>

    <div class="contact">
      <p class="contact__name">KENJI ARAI</p>
      <p class="contact__role">OWNER</p>
      <ul class="contact__list">
        <li class="contact__item">+81 3120-4471
          <svg class="contact__icon" viewBox="0 0 12 12"><path d="M3 1 L5 3.5 L4 5 Q5.5 7.5 7 8 L8.5 7 L11 9 L9.5 11 Q4 10.5 1 3 Z"/></svg>
        </li>
        <li class="contact__item">+81-3120-4472
          <svg class="contact__icon" viewBox="0 0 12 12"><rect x="2" y="1" width="8" height="10" rx="1"/><path d="M4 4 H8 M4 6.5 H8"/></svg>
        </li>
        <li class="contact__item">kenji@sorabean.jp
          <svg class="contact__icon" viewBox="0 0 12 12"><rect x="1" y="2.5" width="10" height="7" rx="1"/><path d="M1 3 L6 7 L11 3"/></svg>
        </li>
        <li class="contact__item">www.sorabeancafe.jp
          <svg class="contact__icon" viewBox="0 0 12 12"><circle cx="6" cy="6" r="5"/><path d="M1 6 H11 M6 1 Q3 6 6 11 Q9 6 6 1"/></svg>
        </li>
      </ul>
    </div>
  </section>

  <section class="card card--logo">
    <svg class="card__art" viewBox="0 0 540 309" preserveAspectRatio="none" aria-hidden="true">
      <defs>
        <linearGradient id="cream-band" x1="0" y1="0" x2="0" y2="1">
          <stop offset="0" stop-color="#f6ead9"/>
          <stop offset="1" stop-color="#e8d3b6"/>
        </linearGradient>
      </defs>
      <path d="M0 196 C150 250 380 248 540 162 V309 H0 Z" fill="url(#cream-band)"/>
      <path d="M0 196 C150 250 380 248 540 162" fill="none" stroke="#3b2518" stroke-width="5"/>
    </svg>

    <div class="brand">
      <span class="brand__square"></span>
      <span class="brand__name">SORA BEAN CAFE</span>
    </div>
  </section>

</main>
</body>
</html>
```